Seeking a new website design for electrical contracting company

Brisket & Vane electrical contracting needs a new website for brisket-vane.example

We are looking for modern and something real cool with motion for a landing page. we have some cool images from our photo shoot. maybe even 3d motion our existing logo. we would like something we can edit with news and events and update a past project page. Also allow to take payment
stock images at
https://lorapellwinphotos.picvault-demo.example/Brisket-and-Vane

Target Market(s)

construction , home owners , business owners,

Industry/Entity Type

construction , electrical

Coding

Number of Pages Required

5+ page

Font styles to use
Serif
Sans Serif

Colors
0054AA
0677BA
7BADD7
CADEEF
E8F1F8
0094D4
00A9DD
6FCCEA
C7EBF8
E9F6FB
FFF300
FFF600
FEFA6F
FFFEC7
FFFEE8

Requirements
Must have
• excitement, motion, selling professionalism,

```html
<!DOCTYPE html>
<html lang="en">
<head>
<meta charset="utf-8">
<title>Brisket &amp; Vane Electrical Contractors</title>
<link href="https://fonts.googleapis.com/css2?family=Poppins:wght@300;400;500;600;700&display=swap" rel="stylesheet">
<style>
:root{
  --blue:#0054AA;
  --blue-2:#0677BA;
  --blue-soft:#E8F1F8;
  --ink:#0c0c0d;
  --white:#ffffff;
  --grey:#f1f2f4;
  --muted:#6b6f76;
  --star:#f5b400;
  --yellow:#FFF300;
}
*{box-sizing:border-box;margin:0;padding:0}
html,body{width:1200px;height:3505px;overflow:hidden}
body{font-family:"Poppins",sans-serif;color:var(--ink);background:var(--white);position:relative}
.abs{position:absolute}
.badge{position:absolute;background:var(--blue);color:#fff;font-size:10px;font-weight:500;padding:0 9px;line-height:20px;letter-spacing:.2px}
.btn{position:absolute;display:flex;align-items:center;justify-content:center;font-size:12px;font-weight:600;color:#fff;border-radius:4px;letter-spacing:.3px}
.btn-dark{background:var(--ink)}
.btn-blue{background:var(--blue)}
.photo{position:absolute}
h1,h2{font-weight:600;letter-spacing:.3px}

/* top bar */
.topbar{left:0;top:0;width:1200px;height:27px;background:var(--ink);color:#fff;font-size:10px}
.topbar .soc{position:absolute;top:9px;width:10px;height:10px;border-radius:2px;background:#fff}
.topbar .info{position:absolute;top:7px;display:flex;align-items:center;gap:5px}
/* header */
.header{left:0;top:27px;width:1200px;height:83px;background:#fff}
.brand{position:absolute;display:flex;align-items:center;gap:8px;font-weight:700;color:var(--blue)}
.brand .mark{border-radius:50%;background:var(--blue)}
.nav{position:absolute;top:35px;font-size:13px;font-weight:500}
.nav.active{color:var(--blue);text-decoration:underline;text-underline-offset:4px;font-weight:600}

/* hero */
.hero-left{left:0;top:110px;width:501px;height:478px;background:linear-gradient(135deg,#1b1e23,#2c3036 60%,#16181c)}
.hero-right{left:501px;top:110px;width:699px;height:478px;background:linear-gradient(160deg,#7a4a3a 0%,#8f8a86 35%,#b9bcbf 60%,#6f7378 100%)}
.hero-title{left:63px;top:255px;font-size:41px;line-height:44px;color:#fff}
.hero-text{left:63px;top:375px;width:370px;font-size:13px;line-height:18px;color:#fff}
.dots{left:561px;top:542px;display:flex;gap:6px}
.dots i{width:6px;height:6px;border-radius:50%;background:#fff;display:block}
.dots i:first-child{background:var(--blue)}

/* about */
.about-title{left:65px;top:733px;font-size:40px;line-height:44px}
.about-text{left:645px;top:738px;width:490px;font-size:15px;line-height:22px}
.ph-team{left:64px;top:841px;width:552px;height:326px;border-radius:8px;background:linear-gradient(180deg,#2a2b2d,#131415)}
.ph-pointer{left:645px;top:913px;width:496px;height:254px;border-radius:8px;background:linear-gradient(120deg,#262729,#4a4b4e 60%,#2e2f31)}
.big-num{left:63px;top:1172px;font-size:76px;font-weight:600;color:var(--blue);line-height:86px}
.big-num span{font-size:54px}
.exp{left:214px;top:1198px;font-size:21px;line-height:29px;font-weight:500}
.partner{position:absolute;top:1220px;height:26px;border-radius:4px;background:#c9cbcf}

/* why */
.why{left:0;top:1324px;width:1200px;height:517px;background:var(--blue)}
.ph-tools{left:65px;top:1382px;width:539px;height:402px;border-radius:4px;background:linear-gradient(135deg,#3a3a3c,#6a5a48 45%,#2f3d52 100%)}
.why-title{left:97px;top:1480px;font-size:40px;line-height:43px;color:#fff}
.why-text{left:97px;top:1600px;width:440px;font-size:15px;line-height:22px;color:#fff}
.stat{position:absolute;width:226px;height:191px;background:#fff;border-radius:3px;text-align:center}
.stat svg{position:absolute;left:50%;top:12px;transform:translateX(-50%)}
.stat .n{position:absolute;left:0;right:0;top:76px;font-size:37px;font-weight:600;line-height:44px}
.stat .l{position:absolute;left:0;right:0;top:135px;font-size:13px;line-height:20px;color:var(--muted)}

/* services */
.sec-title{font-size:38px;line-height:44px}
.card-img{position:absolute;top:2037px;height:226px}
.card-lab{position:absolute;top:2263px;height:54px;background:var(--blue);color:#fff;display:flex;align-items:center;justify-content:center;gap:16px;font-size:17px;font-weight:600;border-radius:0 0 4px 4px}

/* testimonials */
.t-text{left:60px;top:2576px;width:350px;font-size:14px;line-height:19px}
.arrow{position:absolute;top:2664px;width:31px;height:31px;border-radius:50%;background:var(--blue);display:flex;align-items:center;justify-content:center}
.tcard{position:absolute;top:2453px;width:232px;height:200px;background:var(--grey);overflow:hidden}
.tcard .tri{position:absolute;left:0;top:0}
.tcard .av{position:absolute;left:20px;top:20px;width:58px;height:58px;border-radius:50%;border:2px dashed var(--blue);background:#fff;padding:3px}
.tcard .av i{display:block;width:100%;height:100%;border-radius:50%;background:linear-gradient(160deg,#c9b3a4,#6d5a50)}
.tcard .nm{position:absolute;left:84px;top:30px;width:120px;height:40px;background:#fff;padding:6px 8px}
.tcard .nm b{display:block;font-size:11px;font-weight:600;line-height:14px}
.tcard .nm small{display:block;font-size:8px;color:#9aa0a6;line-height:12px}
.tcard .st{position:absolute;left:26px;top:96px;font-size:10px;color:var(--star);letter-spacing:2px}
.tcard .st s{color:#c9ccd1;text-decoration:none}
.tcard p{position:absolute;left:26px;top:122px;width:192px;font-size:9px;line-height:19px;color:#6b6f76}

/* contact */
.c-band{left:0;top:2911px;width:1200px;height:347px;background:linear-gradient(90deg,#0a4aa0,#0054AA 40%,#0a4aa0)}
.c-card{left:141px;top:2759px;width:466px;height:427px;background:#fff}
.c-title{left:174px;top:2820px;font-size:38px;line-height:44px;font-weight:700}
.c-sub{left:174px;top:2880px;width:260px;font-size:11px;line-height:17px;color:#444}
.field{position:absolute;left:178px;width:392px;background:#eef0f2;border:1px solid #d8dbdf;border-radius:6px;font-size:11px;color:#555;padding:8px 12px}
.ph-crew{left:607px;top:2759px;width:370px;height:427px;background:linear-gradient(170deg,#6e3f30 0%,#8f8b88 40%,#4d5055 75%,#2b2d30 100%)}
.c-quote{left:645px;top:3046px;width:260px;font-size:13px;line-height:19px;color:#fff}
.c-name{left:645px;top:3120px;font-size:13px;font-weight:600;color:#fff}
.c-role{left:645px;top:3143px;font-size:9px;color:#fff}

/* footer */
.footer{left:0;top:3258px;width:1200px;height:247px;background:var(--ink);color:#fff}
.f-col{position:absolute;top:49px;font-size:13px}
.f-col h4{color:var(--blue-2);font-size:14px;font-weight:600;margin-bottom:8px}
.f-col li{list-style:none;line-height:27px}
.f-soc{position:absolute;top:128px;width:24px;height:24px;border-radius:50%;background:var(--blue-2)}
.f-line{position:absolute;left:60px;top:198px;width:1080px;height:1px;background:#555}
.f-bottom{position:absolute;top:215px;font-size:10px;color:#ddd}
</style>
</head>
<body>

<!-- top bar -->
<div class="abs topbar">
  <span class="soc" style="left:60px"></span>
  <span class="soc" style="left:94px"></span>
  <span class="soc" style="left:126px"></span>
  <span class="info" style="left:822px">
    <svg width="10" height="9" viewBox="0 0 10 9"><rect x=".5" y=".5" width="9" height="8" fill="none" stroke="#fff"/><path d="M.5 .5l4.5 4 4.5-4" fill="none" stroke="#fff"/></svg>
    hello@brisket-vane.example</span>
  <span class="info" style="left:996px">
    <svg width="8" height="11" viewBox="0 0 8 11"><path d="M4 10.5S.5 6.5.5 4a3.5 3.5 0 017 0c0 2.5-3.5 6.5-3.5 6.5z" fill="none" stroke="#fff"/><circle cx="4" cy="4" r="1.2" fill="#fff"/></svg>
    418 Ember Rd. Dalton, 20417</span>
</div>

<!-- header -->
<header class="abs header">
  <div class="brand" style="left:61px;top:22px;font-size:16px">
    <span class="mark" style="width:36px;height:36px"></span>Brisket &amp; Vane
  </div>
  <nav>
    <a class="nav active" style="left:353px">Home</a>
    <a class="nav" style="left:452px">Service</a>
    <a class="nav" style="left:559px">About</a>
    <a class="nav" style="left:659px">Project</a>
    <a class="nav" style="left:762px">Contact</a>
    <a class="nav" style="left:874px">Blog</a>
  </nav>
  <a class="btn btn-dark" style="left:1022px;top:23px;width:115px;height:36px">BOOK NOW</a>
</header>

<!-- hero -->
<section>
  <div class="photo hero-left" role="img" aria-label="Dark photo of an electrician working on a street beside a parked truck"></div>
  <div class="photo hero-right" role="img" aria-label="Photo of four electricians outdoors reviewing building plans together"></div>
  <span class="badge" style="left:63px;top:204px;font-size:11px;line-height:22px">100% Secure &amp; Reliable Electrician</span>
  <h1 class="abs hero-title">Your Trusted<br>Electrical Services</h1>
  <p class="abs hero-text">Fames metus cras vestibulum torquent blandit in ultrices fermentum urna per quisque egestas feugiat conubia posuere aliquam molestie montes tristique</p>
  <a class="btn btn-blue" style="left:63px;top:461px;width:137px;height:34px">DISCOVER MORE</a>
  <div class="abs dots"><i></i><i></i><i></i><i></i></div>
</section>

<!-- about -->
<section>
  <span class="badge" style="left:65px;top:682px">ABOUT US</span>
  <h2 class="abs about-title">Trusted Electrical Experts<br>Serving</h2>
  <p class="abs about-text">Lorem ipsum dolor sit amet consectetur adipiscing elit velit convallis enim vestibulum sagittis sapien ac inceptos eget sociosqu volutpat integer sem curae nisl magnis montes eros et parturient.</p>
  <a class="btn btn-dark" style="left:645px;top:846px;width:114px;height:36px">READ MORE</a>
  <div class="photo ph-team" role="img" aria-label="Photo of five team members in matching polo shirts standing with arms crossed"></div>
  <div class="photo ph-pointer" role="img" aria-label="Photo of an electrician pointing toward the side"></div>
  <div class="abs big-num">25<span>+</span></div>
  <div class="abs exp">Years of<br>Experience</div>
  <span class="partner" style="left:406px;width:92px"></span>
  <span class="partner" style="left:566px;width:92px;border-radius:13px"></span>
  <span class="partner" style="left:725px;width:82px"></span>
  <span class="partner" style="left:886px;width:84px;border-radius:13px"></span>
  <span class="partner" style="left:1045px;width:95px"></span>
</section>

<!-- why choose us -->
<section>
  <div class="abs why"></div>
  <div class="photo ph-tools" role="img" aria-label="Photo of an electrician's tool belt filled with hand tools"></div>
  <span class="badge" style="left:97px;top:1434px;font-size:9px;line-height:19px">OUR BENIFITIES</span>
  <h2 class="abs why-title">Why you should<br>Choose us</h2>
  <p class="abs why-text">Fames metus cras vestibulum torquent blandit in ultrices fermentum urna per quisque egestas feugiat conubia posuere aliquam molestie montes tristique</p>
  <a class="btn btn-blue" style="left:97px;top:1701px;width:137px;height:33px">DISCOVER MORE</a>

  <div class="stat" style="left:653px;top:1385px">
    <svg width="40" height="56" viewBox="0 0 40 56" fill="none" stroke="#0054AA" stroke-width="2"><path d="M11 2v10M29 2v10"/><rect x="7" y="12" width="8" height="26" rx="2"/><rect x="25" y="12" width="8" height="26" rx="2"/><path d="M11 38v16M29 38v16M7 20h8M7 28h8M25 20h8M25 28h8"/></svg>
    <div class="n">30</div><div class="l">Years Of<br>Experience</div>
  </div>
  <div class="stat" style="left:894px;top:1385px">
    <svg width="48" height="56" viewBox="0 0 48 56" fill="none" stroke="#0054AA" stroke-width="2"><rect x="4" y="4" width="40" height="48" rx="3"/><rect x="14" y="16" width="20" height="24"/><path d="M14 10h20M10 22h4M10 30h4M34 22h4M34 30h4M20 40v6M28 40v6"/></svg>
    <div class="n">2501</div><div class="l">Satisfied<br>Clients</div>
  </div>
  <div class="stat" style="left:653px;top:1592px">
    <svg width="48" height="56" viewBox="0 0 48 56" fill="none" stroke="#0054AA" stroke-width="2"><rect x="14" y="4" width="28" height="46" rx="4"/><rect x="19" y="10" width="18" height="12"/><circle cx="28" cy="34" r="6"/><path d="M6 20v24M6 44c0 6 8 6 8 0"/></svg>
    <div class="n">4500</div><div class="l">Project<br>Complete</div>
  </div>
  <div class="stat" style="left:894px;top:1592px">
    <svg width="52" height="56" viewBox="0 0 52 56" fill="none" stroke="#0054AA" stroke-width="2"><rect x="4" y="6" width="28" height="16" rx="3"/><path d="M32 14h14M14 22v28h12V30M14 40h12"/></svg>
    <div class="n">3020</div><div class="l">Awards Wining<br>Company</div>
  </div>
</section>

<!-- services -->
<section>
  <span class="badge" style="left:60px;top:1935px;font-size:9px;line-height:19px">SERVICES</span>
  <h2 class="abs sec-title" style="left:60px;top:1963px">What We Offer</h2>
  <a class="btn btn-dark" style="left:1000px;top:1967px;width:137px;height:36px">VIEW MORE</a>

  <div class="photo card-img" style="left:60px;width:337px;background:linear-gradient(150deg,#e9e6e0,#c7b89a 45%,#2f4a78 80%)" role="img" aria-label="Photo of a worker with a tool belt and toolbox"></div>
  <div class="card-lab" style="left:60px;width:337px">
    <svg width="24" height="22" viewBox="0 0 24 22" fill="none" stroke="#fff" stroke-width="1.5"><path d="M3 3h18l-2 10H5z M9 3v10M15 3v10M4 8h16M12 13v6M7 19h10"/></svg>House Maintenance</div>

  <div class="photo card-img" style="left:446px;width:321px;background:linear-gradient(140deg,#8d8f92,#c5c7c9 45%,#5e6a74)" role="img" aria-label="Photo of an electrician testing an open electrical panel"></div>
  <div class="card-lab" style="left:446px;width:321px">
    <svg width="24" height="26" viewBox="0 0 24 26" fill="none" stroke="#fff" stroke-width="1.5"><rect x="2" y="2" width="14" height="9" rx="2"/><path d="M16 6h6M7 11v12h6V15M7 18h6"/></svg>Electric Panel Repair</div>

  <div class="photo card-img" style="left:816px;width:321px;background:linear-gradient(180deg,#eef2f8,#cdd6e6 55%,#a9b3c4)" role="img" aria-label="Photo of a bright living room with an air conditioner on the wall"></div>
  <div class="card-lab" style="left:816px;width:321px">
    <svg width="22" height="26" viewBox="0 0 22 26" fill="none" stroke="#fff" stroke-width="1.5"><rect x="7" y="2" width="13" height="22" rx="2"/><rect x="10" y="6" width="7" height="5"/><circle cx="13.5" cy="17" r="3"/><path d="M3 9v12"/></svg>Air Conditioning</div>
</section>

<!-- testimonials -->
<section>
  <span class="badge" style="left:60px;top:2413px;font-size:9px;line-height:19px">TESTIMONIALS</span>
  <h2 class="abs sec-title" style="left:60px;top:2460px;font-size:40px">What Our Clients<br>Are Saying</h2>
  <p class="abs t-text">Fames metus cras vestibulum torquent blandit in ultrices fermentum urna per quisque egestas feugiat conubia posuere aliquam molestie montes tristique</p>
  <span class="arrow" style="left:60px"><svg width="12" height="10" viewBox="0 0 12 10" fill="none" stroke="#fff" stroke-width="1.4"><path d="M11 5H1M5 1L1 5l4 4"/></svg></span>
  <span class="arrow" style="left:99px"><svg width="12" height="10" viewBox="0 0 12 10" fill="none" stroke="#fff" stroke-width="1.4"><path d="M1 5h10M7 1l4 4-4 4"/></svg></span>

  <article class="tcard" style="left:453px">
    <svg class="tri" width="94" height="110" viewBox="0 0 94 110"><path d="M0 0h94L0 110z" fill="#0054AA"/></svg>
    <div class="av" role="img" aria-label="Client portrait"><i></i></div>
    <div class="nm"><b>Gavin Doyle</b><small>Home owner</small></div>
    <div class="st">★★★★<s>★</s></div>
    <p>Build and implement innovative, profitable and sustainable products and services that help</p>
  </article>
  <article class="tcard" style="left:709px">
    <svg class="tri" width="94" height="110" viewBox="0 0 94 110"><path d="M0 0h94L0 110z" fill="#0054AA"/></svg>
    <div class="av" role="img" aria-label="Client portrait"><i></i></div>
    <div class="nm"><b>Mara Quill</b><small>Home owner</small></div>
    <div class="st">★★★★<s>★</s></div>
    <p>Build and implement innovative, profitable and sustainable products and services that help</p>
  </article>
  <article class="tcard" style="left:960px">
    <svg class="tri" width="94" height="110" viewBox="0 0 94 110"><path d="M0 0h94L0 110z" fill="#0054AA"/></svg>
    <div class="av" role="img" aria-label="Client portrait"><i></i></div>
    <div class="nm"><b>Tessa Brandt</b><small>Home owner</small></div>
    <div class="st">★★★★<s>★</s></div>
    <p>Build and implement innovative, profitable and sustainable products and services that help</p>
  </article>
</section>

<!-- contact -->
<section>
  <div class="abs c-band"></div>
  <div class="abs c-card"></div>
  <span class="badge" style="left:174px;top:2789px;font-size:9px;line-height:22px">LET’S CONTACT</span>
  <h2 class="abs c-title">We’re here to help</h2>
  <p class="abs c-sub">Need help with a project or have a question about our work? We’re here for you.</p>
  <div class="field" style="top:2931px;height:32px">Name</div>
  <div class="field" style="top:2975px;height:33px">Email address</div>
  <div class="field" style="top:3019px;height:91px">Message</div>
  <a class="btn btn-dark" style="left:222px;top:3121px;width:305px;height:33px;font-size:11px">SUBMIT REQUEST</a>
  <div class="photo ph-crew" role="img" aria-label="Photo of electricians outdoors discussing building plans"></div>
  <p class="abs c-quote">An insightful consulting firm with an engaged team, providing solutions that blend analytics and creativity.</p>
  <div class="abs c-name">Owen Hale</div>
  <div class="abs c-role">Founder &amp; CEO</div>
</section>

<!-- footer -->
<footer class="abs footer">
  <div class="brand" style="left:60px;top:42px;font-size:23px;color:var(--blue-2)">
    <span class="mark" style="width:56px;height:56px;background:var(--blue-2)"></span>Brisket &amp; Vane
  </div>
  <span class="f-soc" style="left:61px"></span>
  <span class="f-soc" style="left:108px"></span>
  <span class="f-soc" style="left:155px"></span>
  <span class="f-soc" style="left:202px"></span>
  <div class="f-col" style="left:415px"><h4>Quick Link</h4><ul><li>Home</li><li>About</li><li>Service</li><li>Testimonial</li></ul></div>
  <div class="f-col" style="left:658px"><h4>Service</h4><ul><li>Residential</li><li>Commercial</li><li>House Maintenance</li><li>Electric Panel Repair</li></ul></div>
  <div class="f-col" style="left:903px"><h4>Contact Us</h4><ul><li>(555) 014-2290</li><li>office@brisket-vane.example</li><li>72 Copper Lane, Millbrook, Arden</li><li>Help &amp; Contact</li></ul></div>
  <div class="f-line"></div>
  <div class="f-bottom" style="left:60px">All Rights Reserved © 2025 Brisket &amp; Vane Electrical Contractors</div>
  <div class="f-bottom" style="left:927px">Privacy Policy</div>
  <div class="f-bottom" style="left:1036px">Terms &amp; Condition</div>
</footer>

</body>
</html>
```